Tall Fern Roofing Business Card

Need a business card with the logo that was designed here

Contact Information for Business Card

Name, Title, Phone, Email, Website, Company name

```html
<!DOCTYPE html>
<html lang="en">
<head>
<meta charset="utf-8">
<title>Tall Fern Roofing Business Card</title>
<link href="https://fonts.googleapis.com/css2?family=Montserrat:wght@400;600;700&display=swap" rel="stylesheet">
<style>
  :root {
    --bg: #939293;
    --brand-blue: #1b75bc;
    --slate: #8e8e90;
    --white: #ffffff;
    --ink-gray: #8a8a8c;
  }
  * { margin: 0; padding: 0; box-sizing: border-box; }
  html, body { width: 1075px; height: 1200px; overflow: hidden; }
  body {
    background: var(--bg);
    font-family: "Montserrat", sans-serif;
    position: relative;
  }
  .card {
    position: absolute;
    left: 206px;
    width: 663px;
    height: 395px;
    overflow: hidden;
  }
  .card--front { top: 187px; background: var(--white); }
  .card--back { top: 637px; background: var(--brand-blue); }

  .wordmark {
    position: absolute;
    display: flex;
    align-items: center;
    gap: 12px;
    font-weight: 700;
    font-size: 30px;
    letter-spacing: 0.5px;
    white-space: nowrap;
  }
  .wordmark__square { width: 18px; height: 18px; display: block; }
  .card--front .wordmark { right: 44px; top: 92px; color: var(--brand-blue); }
  .card--front .wordmark__square { background: var(--brand-blue); }
  .card--back .wordmark { left: 50%; transform: translateX(-50%); top: 178px; color: var(--white); font-size: 34px; }
  .card--back .wordmark__square { background: var(--white); }

  .person { position: absolute; left: 36px; top: 222px; }
  .person__name { font-size: 22px; font-weight: 700; color: var(--brand-blue); line-height: 1.1; }
  .person__name span { color: var(--slate); }
  .person__title { font-size: 18px; font-weight: 400; color: var(--ink-gray); line-height: 1.2; }
  .person__rule { position: absolute; left: 36px; top: 277px; width: 210px; height: 4px; background: var(--slate); }

  .contact-band {
    position: absolute; left: 0; top: 279px; width: 100%; height: 116px;
    background: var(--brand-blue);
  }
  .contact-list { position: absolute; left: 36px; top: 20px; list-style: none; }
  .contact-list li {
    display: flex; align-items: center; gap: 7px;
    color: var(--white); font-size: 19px; line-height: 24px;
  }
  .contact-list svg { width: 17px; height: 17px; flex: none; }

  .footer-band {
    position: absolute; left: 0; top: 350px; width: 100%; height: 45px;
    background: var(--slate);
    display: flex; align-items: center; justify-content: center;
    color: var(--white); font-size: 18px;
  }
</style>
</head>
<body>
  <section class="card card--front">
    <div class="wordmark"><span class="wordmark__square"></span>Tall Fern Roofing</div>

    <div class="person">
      <p class="person__name">DANIEL <span>HAYES</span></p>
      <p class="person__title">Managing Director</p>
    </div>
    <div class="person__rule"></div>

    <div class="contact-band">
      <ul class="contact-list">
        <li>
          <svg viewBox="0 0 24 24" fill="none" stroke="#fff" stroke-width="2"><path d="M5 3h4l2 5-2.5 1.5a11 11 0 0 0 6 6L16 13l5 2v4a2 2 0 0 1-2 2A16 16 0 0 1 3 5a2 2 0 0 1 2-2z"/></svg>
          044-987 654 321
        </li>
        <li>
          <svg viewBox="0 0 24 24" fill="#fff"><path d="M2 5h20v14H2z"/><path d="M2 5l10 8 10-8" fill="none" stroke="#1b75bc" stroke-width="2"/></svg>
          info@tallfernroofing.com
        </li>
        <li>
          <svg viewBox="0 0 24 24" fill="none" stroke="#fff" stroke-width="2"><circle cx="12" cy="12" r="9"/><path d="M3 12h18M12 3c3 3 3 15 0 18M12 3c-3 3-3 15 0 18"/></svg>
          www.tallfernroofing.com
        </li>
      </ul>
    </div>
  </section>

  <section class="card card--back">
    <div class="wordmark"><span class="wordmark__square"></span>Tall Fern Roofing</div>
    <div class="footer-band">www.tallfernroofing.com</div>
  </section>
</body>
</html>
```